Steadfast Field Crews

We are a underground coal mining labour hire company, needing a website that links into our online payroll (www.wagelinkr.com.au) and also need to have job applications page that is a preform with drop down menu,s with answers or check boxes. We would also need a 3 tier administration access for access to different files.
We are looking for an ongoing relationship with future app integration

Reason: There are a few more designs to come and I'm out at the mine for another week

Industry/Entity Type

Coal Mining

```html
<!DOCTYPE html>
<html lang="en">
<head>
<meta charset="utf-8">
<title>Steadfast Field Crews</title>
<link rel="stylesheet" href="https://fonts.googleapis.com/css2?family=Open+Sans:wght@400;600;700&display=swap">
<style>
:root{
  --black:#000;
  --orange:#f7841e;
  --orange-dark:#e8700c;
  --text:#555;
  --text-dark:#333;
  --link-red:#c0261c;
  --white:#fff;
}
*{margin:0;padding:0;box-sizing:border-box}
html,body{width:893px;height:1200px;overflow:hidden}
body{position:relative;background:var(--white);font-family:"Open Sans",sans-serif;color:var(--text)}
.abs{position:absolute}

.site-header{left:0;top:0;width:893px;height:137px;background:var(--black)}
.crest{left:90px;top:6px;width:120px;height:128px;border-radius:8px;background:radial-gradient(circle at 50% 45%,#f7841e 0,#8a4a12 45%,#1a1a1a 80%)}
.brand{left:232px;top:52px;display:flex;align-items:center;gap:8px;color:var(--white);font-size:26px;font-weight:600}
.brand-dot{width:36px;height:36px;border:3px solid var(--white);border-radius:50%}
.phone{left:546px;top:19px;display:flex;align-items:center;gap:8px;color:var(--orange);font-size:17px;font-weight:700}
.socials{left:716px;top:17px;display:flex;gap:7px}
.social{width:28px;height:28px;border-radius:50%;background:radial-gradient(circle at 40% 35%,#eee,#888);box-shadow:0 2px 3px #000}
.search{left:650px;top:68px;width:160px;height:19px;background:var(--white);border-radius:10px;display:flex;overflow:hidden}
.search span{flex:1;font-size:8px;line-height:19px;padding-left:11px;color:#444}
.search b{width:21px;background:var(--orange)}
.main-nav{left:345px;top:100px;display:flex;height:37px;font-size:11.5px;color:var(--white)}
.main-nav a{line-height:37px;padding:0 8px;color:inherit;text-decoration:none}
.main-nav a.current{background:var(--orange);font-weight:600;padding:0 12px;margin-right:2px}

.hero-band{left:0;top:137px;width:893px;height:305px;background:linear-gradient(90deg,#c9c9c9,#e6e6e6 40%,#d3d3d3)}
.hero{left:72px;top:155px;width:739px;height:288px;border:2px solid var(--white);background:radial-gradient(ellipse at 45% 30%,#6b5138 0,#3a2a1c 45%,#14100c 100%)}
.hero-shadow{left:130px;top:440px;width:600px;height:26px;background:radial-gradient(ellipse at 50% 0,rgba(0,0,0,.35),transparent 70%)}
.hero-arrow{left:91px;top:287px;width:23px;height:23px;border-radius:50%;background:rgba(200,200,200,.7)}
.hero-caption{right:92px;top:346px;text-align:right;color:var(--white);font-weight:700;font-size:13.6px;line-height:26.5px;text-transform:uppercase}

.section-title{left:74px;top:478px;font-size:19px;font-weight:400;color:var(--text-dark)}
.section-title em{font-style:normal;color:var(--orange)}
.card{width:220px;height:107px;border:1px solid #ccc}
.card-label{position:absolute;left:9px;color:var(--white);font-size:14.5px;font-weight:600;line-height:27px}
.bullets{list-style:none;font-size:9.8px;font-weight:600;color:#444;width:240px;white-space:nowrap}
.bullets li{position:relative;padding-left:22px;line-height:18px}
.bullets li::before{content:"";position:absolute;left:5px;top:5px;width:8px;height:8px;border-radius:50%;background:var(--orange)}
.more-link{font-size:11px;color:var(--link-red);display:flex;align-items:center;gap:9px}
.more-link i{width:11px;height:11px;border:1px solid var(--link-red);border-radius:50%}

.welcome-title{left:0;width:893px;top:836px;text-align:center;font-size:19px;font-weight:400;color:var(--text-dark)}
.welcome-title em{font-style:normal;color:var(--orange)}
.welcome-rule{left:85px;top:868px;width:715px;border-top:1px dotted #777}
.welcome-text{left:84px;top:883px;width:722px;font-size:9.6px;line-height:15px;color:#666}
.welcome-text p+p{margin-top:15px}
.btn{background:var(--orange);color:var(--white);text-align:center;border:1px solid #fff;box-shadow:0 0 0 1px var(--orange-dark)}
.welcome-more{left:439px;top:978px;width:60px;height:21px;font-size:10.5px;line-height:20px}

.site-footer{left:0;top:1061px;width:893px;height:139px;background:repeating-linear-gradient(45deg,#3f3f3f 0 2px,#373737 2px 4px)}
.payroll-name{left:82px;top:1084px;display:flex;align-items:center;gap:8px;font-size:30px;color:#7c8fd6}
.payroll-name i{width:26px;height:26px;background:#3944b8}
.news-title{left:366px;top:1081px;font-size:14px;color:var(--white);font-variant:small-caps;letter-spacing:.2px}
.news-input{left:366px;top:1111px;width:175px;height:26px;border-radius:5px;background:linear-gradient(#fff,#e8e8e8);font-size:8px;line-height:26px;padding-left:11px;color:#333}
.subscribe{left:472px;top:1157px;width:68px;height:23px;border-radius:3px;font-size:11px;line-height:22px;box-shadow:none;border:none}
.foot-icons{left:677px;top:1083px;display:flex;gap:9px}
.foot-icons span{width:20px;height:20px}
.copyright{right:85px;top:1121px;text-align:right;font-size:9.6px;line-height:18px;color:#ddd}
</style>
</head>
<body>

<header class="abs site-header">
  <div class="abs crest" role="img" aria-label="Miner emblem artwork for Steadfast Field Crews"></div>
  <div class="abs brand"><span class="brand-dot"></span>SFC</div>
  <div class="abs phone">
    <svg width="18" height="14" viewBox="0 0 18 14"><path d="M1 5c0-3 16-3 16 0v2h-4V5H5v2H1z" fill="#888"/><rect x="4" y="7" width="10" height="7" rx="1" fill="#888"/></svg>
    1-800-4417
  </div>
  <div class="abs socials"><span class="social"></span><span class="social"></span><span class="social"></span></div>
  <div class="abs search"><span>Search</span><b></b></div>
  <nav class="abs main-nav">
    <a class="current">Home</a><a>Apply for Position</a><a>Pay Portal</a><a>Download</a><a>Mission</a><a>About us</a><a>Contact Us</a>
  </nav>
</header>

<div class="abs hero-band"></div>
<div class="abs hero-shadow"></div>
<div class="abs hero" role="img" aria-label="Photo of coal miners in helmets with headlamps underground"></div>
<div class="abs hero-arrow"></div>
<div class="abs hero-caption">Mauris mattis in nunc sit amet<br>rutrum. Nullam cursus odio a<br>risus pellentesque dictum.</div>

<h2 class="abs section-title">Our <em>Services</em></h2>

<div class="abs card" style="left:74px;top:520px;background:linear-gradient(135deg,#6a5646,#2a211a)" role="img" aria-label="Underground mining work photo"><span class="card-label" style="top:80px">Underground</span></div>
<div class="abs card" style="left:326px;top:520px;background:linear-gradient(#3a6bc0,#8fb0dc 60%,#2a2a2a 75%)" role="img" aria-label="Engineer at coal conveyor photo"><span class="card-label" style="top:80px">Engineering</span></div>
<div class="abs card" style="left:582px;top:520px;background:linear-gradient(90deg,#7a6a52,#b9a55a 60%,#6d5b44)" role="img" aria-label="Smiling mine worker in hard hat photo"><span class="card-label" style="top:42px;left:8px">Job Vacancies<br>Apply Now</span></div>
<div class="abs card" style="left:582px;top:647px;background:linear-gradient(90deg,#3b362f,#7a6c4a 50%,#4a4238)" role="img" aria-label="Miners walking in a tunnel photo"><span class="card-label" style="top:54px;left:auto;right:14px;text-align:right">View Employer<br>Benefits</span></div>

<ul class="abs bullets" style="left:74px;top:641px">
  <li>Nam a lacus dictum, laoreet nibh quis.</li>
  <li>Curabitur consectetur adipiscing porttitor.</li>
  <li>Maecenas sollicitudin sodales porta quis.</li>
  <li>Sed vehicula libero eu lobortis dictum.</li>
  <li>Proin pretium nulla eget, commodo dui.</li>
  <li>Proin sapien rhoncus convallis vellibero.</li>
</ul>
<ul class="abs bullets" style="left:326px;top:641px">
  <li>Nam a lacus dictum, laoreet nibh quis.</li>
  <li>Curabitur consectetur adipiscing porttitor.</li>
  <li>Maecenas sollicitudin sodales porta quis.</li>
  <li>Sed vehicula libero eu lobortis dictum.</li>
  <li>Proin pretium nulla eget, commodo dui.</li>
  <li>Proin sapien rhoncus convallis vellibero.</li>
</ul>
<div class="abs more-link" style="left:247px;top:762px">More <i></i></div>
<div class="abs more-link" style="left:499px;top:762px">More <i></i></div>

<h2 class="abs welcome-title">WELCOME TO <em>SFC COAL</em></h2>
<div class="abs welcome-rule"></div>
<div class="abs welcome-text">
  <p>We are KMRT pty ltd trading as Steadfast Field Crews, &nbsp;we are experienced in ground consolidation in underground coal mines, &nbsp;in short when they collapse or cave in we come in with chemical pumps and stabilise the ground or fill cavities which will then allow for the mining process to continue. We also do general mine labor as well.</p>
  <p>We are a labor hire company for major mining services company, &nbsp;we offer labor solutions in New South Wales and Queensland in the underground coal mines.</p>
</div>
<div class="abs btn welcome-more">More</div>

<footer class="abs site-footer"></footer>
<div class="abs payroll-name"><i></i>wagelinkr</div>
<div class="abs news-title">Get FREE Newsletter</div>
<div class="abs news-input">Enter Your Email id</div>
<div class="abs btn subscribe">Subscribe</div>
<div class="abs foot-icons">
  <span style="background:#3b5bb0"></span><span style="background:#3fb3e8"></span><span style="background:#222"></span><span style="background:#f29a1f"></span><span style="background:#d2201f"></span>
</div>
<div class="abs copyright">© 2014 sfccoal.com.au, All Rights Reserved<br>X2</div>

</body>
</html>
```